Wordpress Theme for Medical Clinics

** Please view updated Sitemap2.pdf doc to clarify some confusion ***

This is a multiuser WordPress subscription site for medical clinics. Please see attachment for sitemap. Please do not include extra content like social media icons, search bars, or images. If you have questions, please ask for clarification.
The site contains the following pages and sub-pages:

1. Home
2. Our Clinic
2a. Our Clinic > Mission
2b. Our Clinic > Services
2c. Our Clinic > Clinic Policies
2d. Our Clinic > Schedules
3. Our Staff
3a. Our Staff > [Staff member page]
4. Resources
4a. Resources > Patient Health (index)
4b. Resources > Patient Health (index) > [post]
4c. Resources > Links
4d. Resources > Forms
5. Alerts
5a. Alerts > [Alert Page]
6. Contact Us

Includes the Following Pages, Subpages, and Content
1. Home
a. About Us
b. Our Staff
c. Bulletins
d. Accepting New Patients (shown as an alert widget)
e. Links
i. Physician Toolbox
ii. Book an Appointment
f. Clinic Policies
i. Show first 3 policies (e.g. Late Arrivals, Missed Appointments, Fees)
ii. Link to Clinic Policies page
g. Primary widget (displayed on all pages)
i. Hours of operation
ii. Contact Info
1. Tel
2. Fax
3. Email
4. Address
5. Get directions (link to Google Maps)
2. Our Clinic
a. Main Page
i. Clinic Name
ii. Overview
iii. Languages Spoken
iv. Secondary Navigation
1. Mission
2. Services
3. Clinic Policies
4. Schedules (see attachment)
b. Our Clinic > Mission
c. Our Clinic > Services
i. For each service include service TITLE and DESCRIPTION
d. Our Clinic > Clinic Policies
i. For each policy include policy TITLE and DESCRIPTION
ii. Include the following policies in mockup
1. Late arrivals
2. Missed appointments
3. Fees for missed appointments
4. Referrals and follow-ups
5. Services not covered by RDA
6. Information for LTF patients
7. Medical Legal Reports
e. Our Clinic > Schedules
3. Our Staff
a. Main Page
i. Display a list of staff members. Include NAME and DESIGNATION
b. Our Staff > [Staff Name]
i. Include NAME, PICTURE, DESIGNATION, and BIO
4. Resources
a. Resources > Patient Health
i. Main Page
1. Posts (ordered by date)
a. Title
b. Summary
2. Side Navigation
a. Post Categories
ii. Patient Health > [post title]
1. Title
2. Post Category
3. Date
4. Author
5. Summary
6. Body
b. Resources > Links
1. Secondary Navigation - Categories
a. Sample Categories:
i. Local Services
ii. RDA and Drug Coverage
iii. Mental Health Resources
2. Category page
a. Include the following links in the 'Local Services' category
i. Hypertension clinics
ii. Home Care services
iii. Vaccine Clinics
c. Resources > Forms
i. Display a table with form TITLE and CATEGORY
ii. Side Navigation
1. Form Categories
a. Use the following sample Categories
i. Referrals
ii. Insurance
iii. Intake
iv. Discharge
v. Waivers
5. Alerts
a. Main page
i. List of all Alert posts
1. Include post TITLE as a link to the post
ii. Side Navigation
1. Alerts Archive
a. shown as Month + Number of posts
iii. Alerts > [Alert page]
1. Include TITLE, DATE, AUTHOR, BODY
6. Contact Us
a. Map
b. Hours of operation
c. Address
d. Phone number
e. Fax number
e. Fax number
f. Map
g. Email

Design notes:
- fixed width
- responsive (need designs for mobile, tablet, and desktop)
- simple, dark font, white background
- use Font Awesome icons where needed
- user adds own logo

Target Market(s)

Medical Clinics

Industry/Entity Type

Medical

Number of Pages Required

5+ page

Font styles to use
Serif
Sans Serif

Requirements
Must have
• Please keep designs very simple.
• Examples:
• https://www.quolbin.com/install
• http://www.ventrohax.com/company/about-us
• http://brindlequota.org/
• http://www.trosk.com/
Should not have
• Minimal or no use of shadows and gradients

```html
<!DOCTYPE html>
<html lang="en">
<head>
<meta charset="utf-8">
<title>Cedar Clinic</title>
<link href="https://fonts.googleapis.com/css2?family=Raleway:wght@500;600&family=Open+Sans:wght@400;600&display=swap" rel="stylesheet">
<style>
:root{
  --topbar:#333333;
  --ink:#444444;
  --heading:#1f4e70;
  --brand:#1b6d98;
  --brand-dark:#0f557a;
  --info:#4a8bb3;
  --page:#ebebeb;
  --white:#ffffff;
  --rule:#c9c9c9;
}
*{box-sizing:border-box;margin:0;padding:0}
html,body{width:730px;height:1200px;overflow:hidden}
body{position:relative;background:var(--page);font-family:Arial,"Open Sans",sans-serif;color:var(--ink)}
a{color:inherit}
ul{list-style:none}
.abs{position:absolute}

.topbar{left:0;top:0;width:730px;height:28px;background:var(--topbar);color:#fff;font-size:8.5px}
.topbar .contact{left:61px;top:9px}
.topbar .quick{right:61px;top:9px;word-spacing:1px}

.header{left:0;top:28px;width:730px;height:51px;background:var(--white);border-bottom:1px solid #d5d5d5}
.brand{left:66px;top:14px;display:flex;align-items:center;gap:8px;font-family:Raleway,sans-serif;font-weight:500;font-size:22px;color:var(--brand)}
.brand .mark{width:16px;height:16px;border-radius:50%;background:var(--brand)}
.nav{left:276px;top:0;display:flex;height:51px;font-size:8.5px;color:#222}
.nav li{padding:0 14px;line-height:52px}
.nav li.active{background:#f4f4f4;border-bottom:3px solid var(--brand);line-height:49px;padding:0 10px}

.hero{left:0;top:80px;width:730px;height:265px;background:linear-gradient(90deg,#c9dbe6 0%,#dbe7ee 45%,#e9eef0 65%,#b7cfdc 100%)}
.hero .arrow{top:94px}
.hero .caption{left:61px;top:189px;width:609px;height:61px;background:rgba(40,75,105,.85);color:#fff;font-family:"Open Sans",sans-serif;font-size:8px;line-height:13.5px;padding:10px 11px}

h2.section{font-family:Raleway,sans-serif;font-weight:500;font-size:15px;color:var(--heading);display:flex;align-items:center;gap:8px}
h2.section::after{content:"";height:1px;background:var(--rule);flex:1}

.about-title{left:61px;top:373px;width:378px}
.about-photo{left:61px;top:405px;width:144px;height:110px;background:linear-gradient(135deg,#f1f1f1,#cfd6da 60%,#e6e6e6);border:1px solid #ddd}
.about-text{left:221px;top:404px;width:228px;font-size:8.5px;line-height:12.3px;color:#555}
.about-text p+p{margin-top:12px}

.arrow-list li{font-size:10px;line-height:18.4px;color:#444}
.arrow-list li::before{content:"→";font-size:10px;margin-right:5px}
.staff-title{left:61px;top:556px;width:138px}
.staff-list{left:61px;top:585px}
.links-title{left:271px;top:559px;width:140px}
.links-list{left:271px;top:588px}

.alerts-title{left:62px;top:690px;font-size:15px}
.alert{left:63px;width:367px;font-size:8.2px;line-height:12.2px;color:#444;padding-bottom:8px;border-bottom:1px solid #d6d6d6}
.alert h3{font-size:9px;font-weight:bold;color:#222;margin-bottom:4px}
.alert .more{display:block;color:var(--brand);margin-top:3px;text-decoration:none}
.alert .more::before{content:"→ "}

.card{background:var(--white);border:1px solid #d8d8d8}
.card h2{font-family:Raleway,sans-serif;font-weight:500;font-size:15px;color:var(--heading);border-bottom:1px solid var(--rule);padding-bottom:6px}
.hours{left:480px;top:363px;width:188px;height:318px;padding:11px 16px 0}
.hours table{margin-top:6px;font-size:8px;border-collapse:collapse;width:100%}
.hours td{height:15.9px;color:#333}
.hours td+td{padding-left:28px}
.hours .holiday{font-size:8px;text-decoration:underline;margin-top:1px;display:block}
.contact-card{position:absolute;left:14px;top:185px;width:159px;height:118px;background:var(--info);color:#fff;padding:6px 8px;overflow:hidden}
.contact-card h2{color:#fff;border-color:#b5d1e3;padding-bottom:2px;font-size:14px}
.contact-card dl{display:grid;grid-template-columns:62px 1fr;font-size:8px;row-gap:0;margin-top:4px;line-height:16px}
.contact-card dd{font-size:7.5px;overflow-wrap:anywhere}

.new-patients{left:479px;top:702px;width:190px;height:55px;background:var(--brand);border:3px solid #4a90b8;color:#fff;padding:7px 18px}
.new-patients h2{font-family:Raleway,sans-serif;font-weight:500;font-size:15px}
.new-patients p{font-size:8.5px;margin-top:2px}

.policies{left:480px;top:780px;width:188px;height:182px;padding:11px 12px 0}
.policies h2{width:150px}
.policies ul{margin-top:5px}
.policies li{font-size:8.2px;line-height:18.4px;color:#333}
.policies li::before{content:"→";margin-right:6px}

.footer{left:0;top:999px;width:730px;height:172px;background:var(--brand);color:#fff}
.footer h2{font-family:Raleway,sans-serif;font-weight:600;font-size:14.5px;margin-bottom:6px}
.fcol{top:14px}
.fcol li{font-size:8.3px;line-height:14.6px}
.tri li::before{content:"";display:inline-block;border-left:3px solid #fff;border-top:3px solid transparent;border-bottom:3px solid transparent;margin-right:6px;vertical-align:1px}
.fhours table{font-size:8.3px;border-collapse:collapse}
.fhours td{height:14.6px}
.fhours td+td{padding-left:28px}
.fhours .holiday{font-size:8.3px;text-decoration:underline}
.fcontact li{display:flex;gap:12px;font-size:8.3px;line-height:10px;margin-bottom:12px}
.fcontact svg{flex:none}
.copyright{left:0;top:1171px;width:730px;height:29px;background:var(--brand-dark);color:#fff;font-size:8.3px;text-align:center;line-height:29px}
</style>
</head>
<body>

<div class="abs topbar">
  <span class="abs contact">Telephone 0321550147 &nbsp;|&nbsp; Email care@cedarclinic.ca</span>
  <span class="abs quick">Book an Appointment &nbsp;&nbsp; | &nbsp;&nbsp; Physician Toolbar</span>
</div>

<header class="abs header">
  <div class="abs brand"><span class="mark"></span>Cedar Clinic</div>
  <ul class="abs nav">
    <li class="active">HOME</li><li>OUR CLINIC</li><li>STAFF</li><li>RESOURCES</li><li>ALERTS</li><li>CONTACT US</li>
  </ul>
</header>

<section class="abs hero" role="img" aria-label="Photo of a smiling nurse in blue scrubs with doctors and a patient in a hospital ward behind">
  <svg class="abs arrow" style="left:19px" width="27" height="27" viewBox="0 0 27 27"><circle cx="13.5" cy="13.5" r="12" fill="none" stroke="#777" stroke-width="2"/><path d="M16 7l-6 6.5 6 6.5" fill="none" stroke="#777" stroke-width="2.5"/></svg>
  <svg class="abs arrow" style="left:687px" width="27" height="27" viewBox="0 0 27 27"><circle cx="13.5" cy="13.5" r="12" fill="none" stroke="#777" stroke-width="2"/><path d="M11 7l6 6.5-6 6.5" fill="none" stroke="#777" stroke-width="2.5"/></svg>
  <p class="abs caption">Lorem Ipsum is simply dummy text of the printing and typesetting industry. Lorem Ipsum has been the industry's standard dummy text ever since the 1500s, when an unknown printer took a galley of type and scrambled it to make.It has survived not only five centuries, but also the leap into electronic typesetting, remaining essentially unchanged. It was popularised in the 1960.</p>
</section>

<h2 class="abs section about-title">OUR CLINIC</h2>
<div class="abs about-photo" role="img" aria-label="Photo of a doctor in a white coat writing on a clipboard"></div>
<div class="abs about-text">
  <p>Lorem Ipsum is simply dummy text of the printing and typesetting industry. Lorem Ipsum has been the industry's standard dummy text ever since the 1500s, when an unknown printer took a galley of type and scrambled it to make.</p>
  <p>It has survived not only five centuries, but also the leap into electronic typesetting, remaining essentially unchanged. It was popularised in the 1960.</p>
</div>

<h2 class="abs section staff-title">STAFF</h2>
<ul class="abs arrow-list staff-list">
  <li>Dr Alan Price MD</li><li>Dr Mara Lind MD</li><li>Dr Owen Hale MD</li><li>Dr Ravi Bose MD</li>
</ul>
<h2 class="abs section links-title">LINKS</h2>
<ul class="abs arrow-list links-list">
  <li>Dr Alan Price MD</li><li>Dr Mara Lind MD</li><li>Dr Owen Hale MD</li><li>Dr Ravi Bose MD</li>
</ul>

<h2 class="abs section alerts-title">ALERTS</h2>
<article class="abs alert" style="top:723px">
  <h3>Alert Headline 1</h3>
  Lorem ipsum dolor sit amet, consectetuer adipiscing elit, sed diam nonummy nibh euismod tincidunt ut laoreet dolore dolor sit amet, consectetuer adipiscing elit, sed diam nonummy nibh euismod tincidunt ut laoreet dolore magna aliquam erat volutpat.
  <a class="more" href="#">Read More</a>
</article>
<article class="abs alert" style="top:811px">
  <h3>Alert Headline 1</h3>
  Lorem ipsum dolor sit amet, consectetuer adipiscing elit, sed diam nonummy nibh euismod tincidunt ut laoreet dolore dolor sit amet, consectetuer adipiscing elit, sed diam nonummy nibh euismod tincidunt ut laoreet dolore magna aliquam erat volutpat.
  <a class="more" href="#">Read More</a>
</article>
<article class="abs alert" style="top:897px;left:66px;border-bottom:none">
  <h3>Alert Headline 1</h3>
  Lorem ipsum dolor sit amet, consectetuer adipiscing elit, sed diam nonummy nibh euismod tincidunt ut laoreet dolore dolor sit amet, consectetuer adipiscing elit, sed diam nonummy nibh euismod tincidunt ut laoreet dolore magna aliquam erat volutpat.
  <a class="more" href="#">Read More</a>
</article>

<aside class="abs card hours">
  <h2>Hours Of Operation</h2>
  <table>
    <tr><td>Monday</td><td>8:00 AM - 6:00 PM</td></tr>
    <tr><td>Tusday</td><td>8:00 AM - 6:00 PM</td></tr>
    <tr><td>Wednesday</td><td>8:00 AM - 6:00 PM</td></tr>
    <tr><td>Thursday</td><td>8:00 AM - 6:00 PM</td></tr>
    <tr><td>Friday</td><td>8:00 AM - 6:00 PM</td></tr>
    <tr><td>Satarday</td><td>8:00 AM - 4:00 PM</td></tr>
    <tr><td>Sunday</td><td>8:00 AM - 4:00 PM</td></tr>
  </table>
  <a class="holiday" href="#">Holiday hours</a>
  <div class="contact-card">
    <h2>Contact Info</h2>
    <dl>
      <dt>Telephone</dt><dd>8045550199</dd>
      <dt>Email</dt><dd>care@cedarclinic.ca</dd>
      <dt>Address</dt><dd>456 Elm Road<br>Vancover B.C<br>Canada V2B4DC</dd>
    </dl>
  </div>
</aside>

<aside class="abs new-patients">
  <h2>New Patients</h2>
  <p>Accepting new patients. <a href="#">contact us</a></p>
</aside>

<aside class="abs card policies">
  <h2>Clinic Policies</h2>
  <ul>
    <li>Late Arrivals</li><li>Missed Appointments</li><li>Fees for Missed Appointment</li><li>Referrals and follow ups</li><li>Services not covered by RDA</li><li>Information for LTF Patients</li><li>Medicial Legal Reports</li>
  </ul>
</aside>

<footer class="abs footer">
  <div class="abs fcol" style="left:70px">
    <h2>Our Clinic</h2>
    <ul class="tri"><li>Mission</li><li>Services</li><li>Schdules</li><li>Polices</li><li>Staff</li><li>Alerts</li><li>Contact us</li></ul>
  </div>
  <div class="abs fcol" style="left:186px">
    <h2>Resources</h2>
    <ul class="tri"><li>Our &nbsp;Clinic</li><li>Mission</li><li>Services</li></ul>
  </div>
  <div class="abs fcol fhours" style="left:314px">
    <h2>Hours Of Oprations</h2>
    <table>
      <tr><td>Monday</td><td>8:00 AM - 6:00 PM</td></tr>
      <tr><td>Tusday</td><td>8:00 AM - 6:00 PM</td></tr>
      <tr><td>Wednesday</td><td>8:00 AM - 6:00 PM</td></tr>
      <tr><td>Thursday</td><td>8:00 AM - 6:00 PM</td></tr>
      <tr><td>Friday</td><td>8:00 AM - 6:00 PM</td></tr>
      <tr><td>Satarday</td><td>8:00 AM - 4:00 PM</td></tr>
      <tr><td>Sunday</td><td>8:00 AM - 4:00 PM</td></tr>
    </table>
    <a class="holiday" href="#">Holiday hours</a>
  </div>
  <div class="abs fcol fcontact" style="left:530px">
    <h2>Contact us</h2>
    <ul style="margin-top:10px">
      <li><svg width="11" height="11" viewBox="0 0 24 24"><path fill="#fff" d="M6.6 10.8a15 15 0 006.6 6.6l2.2-2.2c.3-.3.7-.4 1-.2 1.1.4 2.3.6 3.6.6.6 0 1 .4 1 1V20c0 .6-.4 1-1 1A17 17 0 013 4c0-.6.4-1 1-1h3.5c.6 0 1 .4 1 1 0 1.3.2 2.5.6 3.6.1.3 0 .7-.2 1z"/></svg><span>8045550199</span></li>
      <li><svg width="13" height="10" viewBox="0 0 26 20"><rect x="1" y="1" width="24" height="18" fill="#fff"/><path d="M1 1l12 10L25 1M1 19l9-8M25 19l-9-8" fill="none" stroke="#1b6d98" stroke-width="2"/></svg><span>care@cedarclinic.ca</span></li>
      <li><svg width="11" height="15" viewBox="0 0 22 30"><path fill="#fff" d="M11 0a11 11 0 00-11 11c0 8 11 19 11 19s11-11 11-19A11 11 0 0011 0zm0 15a4 4 0 110-8 4 4 0 010 8z"/></svg><span>456 Elm Road<br>Vancover B.C<br>Canada V2B4DC</span></li>
    </ul>
  </div>
</footer>
<div class="abs copyright">Copyright © 2015 Northgate Health Group. All Rights Reserved Terms of Use &nbsp;| &nbsp;Privacy Policy &nbsp;| &nbsp;Sitemap</div>

</body>
</html>
```